Vernac Law Business cards and stationary design project

We are looking for a stationary design for business cards (double sided), 8x10, 5x7, and legal and standard envelopes.

We would like the design to match the logo that we have already.
Color palate preferred is Teal, White, grey and any others that will look good for a professional law firm.

We would like this statement: "RELATIONSHIPS. RESPECT. RESULT" to be on the back of the business cards and maybe on the stationary if it looks good.

Please see link to website for more information: www.vernac-law.example

Target Market(s)

Potential clients that need Attorney services.

Industry/Entity Type

Law Firm

Contact Information for Business Card

We would like the front and back to be two different colors. Current business cards are teal front, grey back and are a vertical design. We are open to options with colors.

Font styles to use
Serif

Colors
33a6d7
33b8a4
b9b9b9
5c5c5c

Requirements
Must have
• Logo supplied needs to go on the card and stationary.
• Match website color palate, www.vernac-law.example
• Be professional and not too wordy.
• Criminal Law, Civil Litigation, Personal Injury, Restraining Orders need to be on the card.
Nice to have
• RELATIONSHIPS. RESPECT. RESULTS. on the back of the card.
Should not have
• Not be too busy/wordy or too flashy.

```html
<!DOCTYPE html>
<html lang="en">
<head>
<meta charset="utf-8">
<title>Vernac Law Letterhead</title>
<link href="https://fonts.googleapis.com/css2?family=Source+Sans+3:wght@400;600;700&display=swap" rel="stylesheet">
<style>
  :root {
    --backdrop: #c4c4c4;
    --paper: #ececec;
    --teal: #1b7f8c;
    --teal-line: #2a8fa0;
    --ink: #5a5a5a;
    --ink-dark: #222222;
    --band: #555555;
    --band-text: #f2f2f2;
    --signature-tone: #3a3a3a;
  }
  * { box-sizing: border-box; margin: 0; padding: 0; }
  html, body {
    width: 1200px; height: 1193px; overflow: hidden;
    background: var(--backdrop);
    font-family: "Source Sans 3", "Myriad Pro", Arial, sans-serif;
  }
  .letterhead {
    position: absolute; left: 155px; top: 20px;
    width: 891px; height: 1153px;
    background: var(--paper);
    box-shadow: 0 6px 24px rgba(0,0,0,0.25);
  }
  .brand {
    position: absolute; left: 81px; top: 190px;
    display: flex; align-items: center; gap: 12px;
  }
  .brand-mark {
    width: 14px; height: 14px; background: var(--teal);
  }
  .brand-name {
    font-size: 40px; font-weight: 400; letter-spacing: 2px;
    color: var(--teal); line-height: 1;
  }
  .address-block {
    position: absolute; left: 81px; top: 340px;
    color: var(--ink); font-size: 15.5px; line-height: 1;
  }
  .address-block .date { margin-bottom: 14px; }
  .address-block .recipient { margin-bottom: 10px; }
  .address-block .company,
  .address-block .locality { font-size: 16.5px; margin-bottom: 6px; }
  .salutation {
    position: absolute; left: 81px; top: 487px;
    color: var(--ink); font-size: 15.5px;
  }
  .letter-body {
    position: absolute; left: 81px; top: 526px; width: 740px;
    color: var(--ink); font-size: 15.5px; line-height: 21.3px;
  }
  .letter-body p { text-indent: 8px; margin-bottom: 20.5px; }
  .signature {
    position: absolute; left: 81px; top: 914px;
    width: 153px; height: 58px;
    background: linear-gradient(90deg, rgba(58,58,58,0.18), rgba(58,58,58,0.06));
    border-radius: 4px;
  }
  .signer {
    position: absolute; left: 84px; top: 976px;
    color: var(--ink-dark); font-size: 18px; font-weight: 700;
  }
  .footer-rule {
    position: absolute; left: 0; top: 1098px; width: 100%;
    height: 3px; background: var(--teal-line);
  }
  .footer-band {
    position: absolute; left: 0; top: 1102px; width: 100%; height: 51px;
    background: var(--band);
    display: flex; align-items: center; justify-content: center; gap: 10px;
    color: var(--band-text); font-size: 14.5px;
  }
  .contact { display: flex; align-items: center; gap: 5px; white-space: nowrap; }
  .contact svg { width: 12px; height: 12px; fill: var(--teal-line); }
</style>
</head>
<body>
  <main class="letterhead">
    <div class="brand">
      <span class="brand-mark"></span>
      <span class="brand-name">VERNAC LAW</span>
    </div>

    <div class="address-block">
      <div class="date">December 24, 2015,</div>
      <div class="recipient">To: Evan Marlowe</div>
      <div class="company">Northgate Holdings</div>
      <div class="locality">City,State,Zip</div>
    </div>

    <div class="salutation">Dear Mr Marlowe.</div>

    <div class="letter-body">
      <p>Lorem ipsum dolor sit amet, consectetur adipisicing elit, sed do eiusmod carte incididunt ut labore et dolore magna aliqua. Ut enim ad minim veniam, quis exercitation ullamco laboris nisi ut aliquip ex ea commodo consequat. review dolor in reprehenderit in voluptate .</p>
      <p>build voluptas sit aspernatur aut odit aut fugit, sed quia consequunture fugite ratione voluptatem equi nesciunt. Neque porro quisquam est, qui dolor ipsum sit amet, consectetur, adipisci velit, sed quia non numquam eius modilos iduim labore et dolore .</p>
      <p>Excepteur sint occaecat cupidatat non proident, sunt in culpa qui officia deser accusantium dolore mque laudantium, totam rem aperiam, eaque ipsa quae an ratione voluptatem sequi nesciunt. Nequ porro quisquam est, qui dolorem ie anim id est laborum. Sed ut perspiciatis unde omnis iste natus error sit volupte accusantium doloremque laudantium, totam rem aperiam, eaque ipsa quae ab verit atis et quasi architecto beatae vitae .</p>
      <p>Fuia voluptas sit aspernatur aut odit aut fugit, sed quia consequuntur magni ratione voluptatem sequi nesciunt. Neque porro quisquam est, qui dolorem eps sit amet, consectetur, adipisci velit, sed quia non numquam eius modi tempora labore et dolore .</p>
    </div>

    <div class="signature" role="img" aria-label="Handwritten signature"></div>
    <div class="signer">Daniel Reyes</div>

    <div class="footer-rule"></div>
    <footer class="footer-band">
      <span class="contact">
        <svg viewBox="0 0 12 12"><path d="M6 0a4 4 0 0 0-4 4c0 3 4 8 4 8s4-5 4-8a4 4 0 0 0-4-4zm0 5.6a1.6 1.6 0 1 1 0-3.2 1.6 1.6 0 0 1 0 3.2z"/></svg>
        480 Harbor View Ave. #300 , Seaside Bay, CA 90000
      </span>
      <span class="contact">
        <svg viewBox="0 0 12 12"><path d="M2.4 0.6l2 2.2-1 1.4a7 7 0 0 0 4.4 4.4l1.4-1 2.2 2-1.2 1.8C5.6 11.4 0.6 6.4 0.6 1.8z"/></svg>
        (555) 014-2290
      </span>
      <span class="contact">
        <svg viewBox="0 0 12 12"><path d="M0 2h12v8H0z" opacity=".9"/><path d="M0 2l6 4.5L12 2" fill="none" stroke="#555" stroke-width="1"/></svg>
        mara@vernac-law.example
      </span>
      <span class="contact">
        <svg viewBox="0 0 12 12"><circle cx="6" cy="6" r="6"/><path d="M0 6h12M6 0c-3 3-3 9 0 12M6 0c3 3 3 9 0 12" fill="none" stroke="#555" stroke-width=".8"/></svg>
        www.vernac-law.example
      </span>
    </footer>
  </main>
</body>
</html>
```